I would like a single page website for Skyward Rentals Pacific. In the file list provided there is basic information to be included as well as our logo with colors, fonts and images to be included.
Site must be very simple and be able to be loaded onto smart phones etc very quickly.
Site needs to be very smart in appearance

Target Market(s)

All prospective drone customers from Police to Parties.

Industry/Entity Type

Hire

Requirements
Must have
• Must have variation of color schemes supplied
Nice to have
• Must be very eye catching without going over the top
Should not have
• Anything slow to load.

```html
<!DOCTYPE html>
<html lang="en">
<head>
<meta charset="utf-8">
<title>Skyward Rentals Pacific</title>
<link rel="stylesheet" href="https://fonts.googleapis.com/css2?family=Barlow:wght@500;600;700&family=Exo+2:wght@500;600&family=Open+Sans:wght@400;600;700&display=swap">
<style>
:root{
  --navy:#25305a;
  --navy-soft:#3a4775;
  --navy-deep:#2b3558;
  --grey-bg:#eeeff1;
  --grey-btn:#7b7f8c;
  --text:#555a66;
  --text-light:#8a8f9b;
  --white:#ffffff;
  --accent-link:#8fa0d8;
}
*{box-sizing:border-box;margin:0;padding:0}
html,body{width:1200px;height:2323px;overflow:hidden}
body{position:relative;background:var(--white);font-family:"Open Sans",Arial,sans-serif;color:var(--text)}
.abs{position:absolute}

/* header */
.site-header{left:0;top:0;width:1200px;height:153px;background:var(--white)}
.brand{left:80px;top:52px;display:flex;align-items:center;gap:10px}
.brand-dot{width:14px;height:14px;border-radius:50%;background:#4a5580}
.brand-name{font-family:"Barlow",sans-serif;font-weight:700;color:#4a5580;font-size:25px;line-height:1.05;letter-spacing:1px}
.brand-name span{display:block;letter-spacing:7px}
.nav-active{left:426px;top:0;width:77px;height:133px;background:var(--navy)}
.nav{left:426px;top:104px;display:flex;font-family:"Barlow",sans-serif;font-size:13px;font-weight:500;color:#3c4260;letter-spacing:.3px}
.nav a{text-decoration:none;color:inherit;text-align:center}
.nav .home{width:77px;color:var(--white)}
.call{left:930px;top:38px;font-size:11px;color:#555}
.call strong{font-family:"Barlow",sans-serif;font-size:15px;color:var(--navy);font-weight:600;margin-left:6px}
.call-line{left:912px;top:74px;width:162px;height:2px;background:#e6e7ea}

/* hero */
.hero{left:0;top:153px;width:1200px;height:417px;background:linear-gradient(180deg,#6f7c5e 0%,#8a8a77 40%,#5d6a72 70%,#7b756a 100%)}
.hero-title{left:300px;top:300px;width:830px;text-align:center;font-family:"Barlow",sans-serif;font-weight:700;color:var(--white);line-height:1.2;text-shadow:0 2px 6px rgba(0,0,0,.4)}
.hero-title .l1{font-size:41px;display:block}
.hero-title .l2{font-size:52px;display:block}
.arrow-btn{top:332px;width:42px;height:44px;background:var(--white);display:flex;align-items:center;justify-content:center}

/* services */
.services-bg{left:0;top:570px;width:1200px;height:400px;background:var(--grey-bg)}
.card{top:514px;width:324px;height:398px;background:var(--navy)}
.card-head{height:56px;display:flex;align-items:center;justify-content:center;font-family:"Barlow",sans-serif;font-weight:700;font-size:22px;color:var(--white);letter-spacing:.5px}
.card-media{height:185px}
.card-body{padding:20px 28px 0;text-align:center;font-size:11.5px;line-height:21px;color:#e2e5ef}
.card-btn{display:block;margin:22px auto 0;width:90px;height:26px;background:var(--grey-btn);color:var(--white);font-size:11.5px;font-weight:700;line-height:26px;text-align:center;box-shadow:0 2px 3px rgba(0,0,0,.35)}

/* welcome */
.welcome-title{left:0;top:1005px;width:1200px;text-align:center;font-family:"Exo 2",sans-serif;font-weight:600;font-size:28px;color:var(--navy);letter-spacing:1px}
.welcome-rule{left:472px;top:1057px;width:256px;height:3px;background:var(--navy)}
.welcome-sub{left:0;top:1083px;width:1200px;text-align:center;font-size:15.5px;font-weight:600;color:#6a6e78}
.welcome-text{left:220px;top:1124px;width:760px;text-align:center;font-size:11.5px;line-height:25px;color:#5d616b}
.video{left:265px;top:1207px;width:670px;height:349px;background:linear-gradient(180deg,#4f5664 0%,#6f5f66 40%,#c47a55 62%,#2c3340 78%,#1d2229 100%)}
.video-controls{left:265px;top:1520px;width:670px;height:36px;background:#15181d}

/* blog */
.blog-bg{left:0;top:1602px;width:1200px;height:459px;background:var(--grey-bg)}
.section-title{font-family:"Exo 2",sans-serif;font-weight:600;font-size:17px;color:var(--navy);letter-spacing:1px}
.post-media{top:1692px;width:302px;height:178px;border-bottom:8px solid var(--navy)}
.post-title{top:1893px;font-family:"Barlow",sans-serif;font-weight:600;font-size:16px;color:var(--navy)}
.post-text{top:1925px;width:302px;font-size:11px;line-height:23px;color:var(--text-light)}
.post-text b{font-weight:400;color:var(--navy);margin-left:14px;font-size:12px}
.post-rule{top:1986px;width:302px;height:1px;background:#d4d6db}
.post-meta{top:2003px;display:flex;gap:14px;font-size:11px;color:#555a66}
.post-meta span{display:flex;align-items:center;gap:6px}
.services-list{left:780px;top:1690px;list-style:none}
.services-list li{display:flex;align-items:center;gap:14px;height:32px;font-size:11.5px;color:#5d616b}

/* footer */
.footer{left:0;top:2061px;width:1200px;height:220px;background:var(--navy-soft)}
.foot-head{top:2100px;font-family:"Open Sans",sans-serif;font-weight:700;font-size:14px;color:#8d97bb}
.foot-links{top:2135px;list-style:none;font-size:11px;line-height:26.5px;color:var(--white)}
.foot-note{left:555px;top:2133px;width:210px;font-size:11px;line-height:26px;color:var(--white)}
.news-input{left:555px;top:2196px;width:180px;height:36px;background:var(--white)}
.news-btn{left:735px;top:2196px;width:73px;height:36px;background:var(--grey-btn);color:var(--white);font-size:11px;line-height:36px;text-align:center}
.copyright{left:0;top:2281px;width:1200px;height:42px;background:var(--navy-deep);text-align:center;line-height:42px;font-size:11px;color:var(--white)}
.copyright span{color:var(--accent-link)}
</style>
</head>
<body>

<header class="abs site-header">
  <div class="abs brand"><div class="brand-dot"></div><div class="brand-name">SKYWARD RENTALS<span>PACIFIC</span></div></div>
  <div class="abs nav-active"></div>
  <nav class="abs nav">
    <a class="home">HOME</a>
    <a style="width:106px">ABOUT US</a>
    <a style="width:128px">SERVICES</a>
    <a style="width:72px">NEWS</a>
    <a style="width:88px">BLOG</a>
    <a style="width:102px">CONTACT</a>
    <a style="width:62px"><svg width="13" height="13" viewBox="0 0 13 13"><circle cx="5.5" cy="5.5" r="4" fill="none" stroke="#25305a" stroke-width="2"/><line x1="8.5" y1="8.5" x2="12" y2="12" stroke="#25305a" stroke-width="2.2"/></svg></a>
  </nav>
  <div class="abs call">Call Us: <strong>0400 315 902</strong></div>
  <div class="abs call-line"></div>
</header>

<section class="abs hero" role="img" aria-label="Aerial view of a riverside city with a white quadcopter drone in flight"></section>
<h1 class="abs hero-title"><span class="l1">SURVEILLANCE IN LAUNCESTON,</span><span class="l2">AUSTRALIA</span></h1>
<div class="abs arrow-btn" style="left:0"><svg width="12" height="16" viewBox="0 0 12 16"><path d="M9 2 3 8l6 6" fill="none" stroke="#25305a" stroke-width="3"/></svg></div>
<div class="abs arrow-btn" style="left:1158px"><svg width="12" height="16" viewBox="0 0 12 16"><path d="M3 2l6 6-6 6" fill="none" stroke="#25305a" stroke-width="3"/></svg></div>

<div class="abs services-bg"></div>
<article class="abs card" style="left:80px">
  <div class="card-head">SURVEILLANCE</div>
  <div class="card-media" role="img" aria-label="Drone flying over coastal sea stacks" style="background:linear-gradient(180deg,#7fa6cf 0%,#b58f5e 55%,#3f7fa0 100%)"></div>
  <div class="card-body">Lorem ipsum dolor sit amet conse ctetur adipisicing elit, sed do eiusmod tempor incididunt ut labore et dolore magna aliqua.<span class="card-btn">More Info</span></div>
</article>
<article class="abs card" style="left:438px">
  <div class="card-head">SECURITY</div>
  <div class="card-media" role="img" aria-label="White drone hovering over a green valley" style="background:linear-gradient(180deg,#c9d3d8 0%,#6f8a6a 45%,#3c5c3a 100%)"></div>
  <div class="card-body">Lorem ipsum dolor sit amet conse ctetur adipisicing elit, sed do eiusmod tempor incididunt ut labore et dolore magna aliqua.<span class="card-btn">More Info</span></div>
</article>
<article class="abs card" style="left:796px">
  <div class="card-head">PARTIES</div>
  <div class="card-media" role="img" aria-label="Drone above a pumpkin patch party with a navy overlay" style="background:linear-gradient(180deg,#5a68a8 0%,#3b4a8c 55%,#56608f 100%)"></div>
  <div class="card-body">Lorem ipsum dolor sit amet conse ctetur adipisicing elit, sed do eiusmod tempor incididunt ut labore et dolore magna aliqua.<span class="card-btn">More Info</span></div>
</article>

<h2 class="abs welcome-title">WELCOME!</h2>
<div class="abs welcome-rule"></div>
<p class="abs welcome-sub">WE GIVE DRONES ON HIRE FOR PARTIES, SURVEILLANCE, SECURITY ETC..</p>
<p class="abs welcome-text">CASA certified company and CASA endorsed pilot, with Full Public Liability Insurance. All operating licences are in place and are carried on the operator. All drones are maintained to full CASA compliance standards</p>
<div class="abs video" role="img" aria-label="Video still of a drone launched by hand against a sunset sky"></div>
<svg class="abs" style="left:559px;top:1340px" width="82" height="56" viewBox="0 0 82 56"><rect width="82" height="56" rx="12" fill="rgba(20,24,32,.75)"/><path d="M32 16v24l20-12z" fill="#fff"/></svg>
<svg class="abs" style="left:862px;top:1222px" width="52" height="20" viewBox="0 0 52 20"><path d="M9 17 2 10a4 4 0 0 1 7-5 4 4 0 0 1 7 5z" fill="#1b1e24"/><g fill="none" stroke="#1b1e24" stroke-width="2.2"><rect x="31" y="9" width="9" height="5" rx="2.5" transform="rotate(-40 35 11)"/><rect x="38" y="5" width="9" height="5" rx="2.5" transform="rotate(-40 42 7)"/></g></svg>
<div class="abs video-controls"></div>
<svg class="abs" style="left:265px;top:1520px" width="670" height="36" viewBox="0 0 670 36">
  <path d="M16 12v12l10-6z" fill="#fff"/>
  <rect x="60" y="16" width="155" height="5" rx="2" fill="#3b4f85"/>
  <rect x="215" y="16" width="150" height="5" rx="2" fill="#2a2e36"/>
  <rect x="190" y="13" width="18" height="11" rx="2" fill="#d8dbe2"/>
  <text x="405" y="22" font-family="Open Sans, sans-serif" font-size="11" fill="#fff">4.25 / 7.12</text>
  <path d="M497 14h4l5-4v16l-5-4h-4z" fill="#fff"/>
  <rect x="527" y="16" width="80" height="5" rx="2" fill="#fff"/>
  <path d="M640 11h-5v5M651 11h5v5M640 25h-5v-5M651 25h5v-5" fill="none" stroke="#fff" stroke-width="2"/>
</svg>

<div class="abs blog-bg"></div>
<h3 class="abs section-title" style="left:80px;top:1644px">LATEST BLOG</h3>
<h3 class="abs section-title" style="left:780px;top:1644px">SPECIALIZED SERVICES</h3>

<div class="abs post-media" style="left:80px" role="img" aria-label="Two-storey house with a shingled roof under a blue sky" style2="" ></div>
<div class="abs post-media" style="left:80px;background:linear-gradient(180deg,#5f8fd2 0%,#8fa59a 45%,#6b7a63 75%,#a3865e 100%)" role="img" aria-label="Two-storey house with a shingled roof under a blue sky"></div>
<div class="abs post-media" style="left:418px;background:linear-gradient(180deg,#b99a55 0%,#a0783e 55%,#7d5a2e 100%)" role="img" aria-label="Pet dog resting in long dry grass"></div>

<h4 class="abs post-title" style="left:80px">Roof Inspection in Sydney</h4>
<h4 class="abs post-title" style="left:418px">Lost My Pet Dog</h4>
<p class="abs post-text" style="left:80px">Aliquam dapibus tincidunt metus. Praesent justo dolor, lobortis quis, lobor, pulvinar ac.........<b>&gt;&gt; More</b></p>
<p class="abs post-text" style="left:418px">Aliquam dapibus tincidunt metus. Praesent justo dolor, lobortis quis, lobor, pulvinar ac.........<b>&gt;&gt; More</b></p>
<div class="abs post-rule" style="left:80px"></div>
<div class="abs post-rule" style="left:418px"></div>

<div class="abs post-meta" style="left:80px">
  <span><svg width="10" height="12" viewBox="0 0 10 12"><path d="M0 0h7l3 3v9H0z" fill="#3c4260"/></svg>5 Comments</span>
  <span><svg width="11" height="11" viewBox="0 0 11 11"><circle cx="5.5" cy="3" r="3" fill="#3c4260"/><path d="M0 11a5.5 4.5 0 0 1 11 0z" fill="#3c4260"/></svg>Super User</span>
  <span><svg width="11" height="11" viewBox="0 0 11 11"><rect y="1" width="11" height="10" fill="none" stroke="#3c4260" stroke-width="1.6"/><rect y="1" width="11" height="3" fill="#3c4260"/></svg>April 28, 2015</span>
</div>
<div class="abs post-meta" style="left:418px">
  <span><svg width="10" height="12" viewBox="0 0 10 12"><path d="M0 0h7l3 3v9H0z" fill="#3c4260"/></svg>5 Comments</span>
  <span><svg width="11" height="11" viewBox="0 0 11 11"><circle cx="5.5" cy="3" r="3" fill="#3c4260"/><path d="M0 11a5.5 4.5 0 0 1 11 0z" fill="#3c4260"/></svg>Super User</span>
  <span><svg width="11" height="11" viewBox="0 0 11 11"><rect y="1" width="11" height="10" fill="none" stroke="#3c4260" stroke-width="1.6"/><rect y="1" width="11" height="3" fill="#3c4260"/></svg>April 28, 2015</span>
</div>

<ul class="abs services-list">
  <li><svg width="13" height="13" viewBox="0 0 13 13"><path d="M13 0 0 6l5 2 2 5z" fill="#3c4260"/></svg>Special Occasions, Childrens Birthday Parties, Wedding</li>
  <li><svg width="13" height="13" viewBox="0 0 13 13"><path d="M13 0 0 6l5 2 2 5z" fill="#3c4260"/></svg>Sporting events</li>
  <li><svg width="13" height="13" viewBox="0 0 13 13"><path d="M13 0 0 6l5 2 2 5z" fill="#3c4260"/></svg>Real Estate Brochures</li>
  <li><svg width="13" height="13" viewBox="0 0 13 13"><path d="M13 0 0 6l5 2 2 5z" fill="#3c4260"/></svg>Construction project updates for remote stake holders</li>
  <li><svg width="13" height="13" viewBox="0 0 13 13"><path d="M13 0 0 6l5 2 2 5z" fill="#3c4260"/></svg>Surveillance – Police, Local councils worksafe etc</li>
  <li><svg width="13" height="13" viewBox="0 0 13 13"><path d="M13 0 0 6l5 2 2 5z" fill="#3c4260"/></svg>Building/Roof Condition Inspections</li>
  <li><svg width="13" height="13" viewBox="0 0 13 13"><path d="M13 0 0 6l5 2 2 5z" fill="#3c4260"/></svg>Lost pets</li>
  <li><svg width="13" height="13" viewBox="0 0 13 13"><path d="M13 0 0 6l5 2 2 5z" fill="#3c4260"/></svg>Real Estate Brochures</li>
  <li><svg width="13" height="13" viewBox="0 0 13 13"><path d="M13 0 0 6l5 2 2 5z" fill="#3c4260"/></svg>Accident reconstructions</li>
  <li><svg width="13" height="13" viewBox="0 0 13 13"><path d="M13 0 0 6l5 2 2 5z" fill="#3c4260"/></svg>Insurance assessing</li>
</ul>

<footer class="abs footer"></footer>
<h5 class="abs foot-head" style="left:120px">Quick Links</h5>
<h5 class="abs foot-head" style="left:328px">Information</h5>
<h5 class="abs foot-head" style="left:555px">Sign up for Newsletter</h5>
<h5 class="abs foot-head" style="left:907px">Follow Us</h5>
<ul class="abs foot-links" style="left:120px"><li>Home</li><li>Featured Services</li><li>Blog</li><li>About Us</li></ul>
<ul class="abs foot-links" style="left:328px"><li>Site Map</li><li>Terms and Conditions</li><li>Policy</li><li>Contact Us</li></ul>
<p class="abs foot-note">Subscribe for getting latest news and updates.</p>
<div class="abs news-input"></div>
<div class="abs news-btn">Subscribe</div>
<svg class="abs" style="left:906px;top:2146px" width="175" height="50" viewBox="0 0 175 50" aria-label="Social links">
  <path d="M27 2 54 48H0z" fill="#2f6fd6"/>
  <path d="M86 2l27 46H59z" fill="#3ca45a"/>
  <path d="M146 2l28 46h-56z" fill="#e0565e"/>
</svg>
<div class="abs copyright">© 2015 <span>Skyward Rentals Pacific</span>. All rights reserved.</div>

</body>
</html>
```